Business Card for a mobile physiotherapy company

I need a layout for a business card for a mobile physiotherapy company.
Slogan is "Mobile Physiotherapy - Your Road To Recovery"
Phone number is 867-555-0142
Email VardenTherapy@postnest.ca (subject to change with website)
Website www.VardenTherapy.ca
My name and credentials: Luke Varden Luke Varden, BSc(kin), MPT, CAFCI, IMS
Information maybe included: Direct Billing, Services including Physiotherapy, IMS, acupuncture
Maybe include facebook and instagram logos
One side with the logo clean and sharp
Other side with details, try not to look too busy, keep everything concise

```html
<!DOCTYPE html>
<html lang="en">
<head>
<meta charset="utf-8">
<title>Varden Therapy – Business Card</title>
<link rel="stylesheet" href="https://fonts.googleapis.com/css2?family=Open+Sans:wght@400;600;700&family=Tinos:wght@700&display=swap">
<style>
  :root {
    --navy: #2c4a71;
    --green: #0d5a48;
    --white: #ffffff;
    --ink: #1f2d3d;
    --rule: #a7a9ac;
    --stage: #d6d7d9;
  }
  * { box-sizing: border-box; margin: 0; padding: 0; }
  html, body { width: 1200px; height: 1114px; overflow: hidden; }
  body {
    background: var(--stage);
    position: relative;
    font-family: "Open Sans", Arial, sans-serif;
  }
  .card {
    position: absolute;
    width: 767px;
    height: 440px;
    border-radius: 34px;
    overflow: hidden;
  }
  .card--front { left: 88px; top: 80px; background: var(--white); border: 1px solid #9ea0a3; }
  .card--back { left: 352px; top: 584px; background: var(--navy); }

  .wave { position: absolute; left: 0; top: 0; width: 100%; height: 100%; }

  /* Brand block: plain placeholder mark + name in the body text font */
  .brand { position: absolute; text-align: center; }
  .brand__mark { display: block; margin: 0 auto; border-radius: 50%; }
  .brand__name {
    display: block;
    font-family: "Open Sans", Arial, sans-serif;
    font-weight: 700;
    line-height: 1.1;
  }
  .card--front .brand { left: 39px; top: 52px; width: 340px; }
  .card--front .brand__mark { width: 132px; height: 132px; background: var(--navy); }
  .card--front .brand__name { font-size: 34px; color: var(--navy); margin-top: 44px; }
  .card--back .brand { left: 0; top: 50px; width: 100%; }
  .card--back .brand__mark { width: 134px; height: 134px; background: var(--white); }
  .card--back .brand__name { font-size: 40px; color: var(--white); margin-top: 48px; }

  .divider {
    position: absolute; left: 393px; top: 42px;
    width: 3px; height: 256px; background: var(--rule);
  }

  .details { position: absolute; left: 427px; top: 36px; color: var(--ink); }
  .details__name {
    font-family: "Tinos", "Times New Roman", serif;
    font-weight: 700;
    font-size: 27px; letter-spacing: 1px; color: var(--navy);
  }
  .details__creds { font-size: 14.5px; }
  .contact { list-style: none; margin-top: 16px; }
  .contact li { display: flex; align-items: center; font-size: 18.5px; height: 32px; }
  .contact svg { width: 19px; height: 19px; margin-right: 7px; flex: none; }
  .services__title { font-size: 18.5px; font-weight: 700; color: var(--navy); margin-top: 16px; }
  .services__row {
    display: flex; color: var(--green); font-size: 18.5px; line-height: 27px;
  }
  .services__row:first-of-type { margin-top: 7px; }
  .services__row span::before { content: "\2022\00a0"; }
  .services__row span + span { margin-left: 13px; }
  .services__row--second span + span { margin-left: 16px; }

  .slogan {
    position: absolute; left: 0; bottom: 24px; width: 100%;
    text-align: center; color: var(--white);
    font-family: "Tinos", "Times New Roman", serif;
    font-weight: 700;
    font-size: 18.5px; letter-spacing: .3px;
  }

  .social {
    position: absolute; left: 0; top: 345px; width: 100%;
    display: flex; justify-content: center; gap: 26px;
    color: var(--white); font-size: 21px;
  }
  .social__item { display: flex; align-items: center; gap: 10px; }
  .social__mark { width: 46px; height: 46px; background: var(--white); border-radius: 6px; }
</style>
</head>
<body>

<section class="card card--front" aria-label="Front of business card">
  <svg class="wave" viewBox="0 0 720 413" preserveAspectRatio="none" aria-hidden="true">
    <path d="M0,240 C40,320 160,352 300,346 C440,340 580,298 720,283" fill="none" stroke="var(--navy)" stroke-width="3"/>
    <path d="M0,256 C50,336 170,362 300,356 C440,349 575,306 720,292" fill="none" stroke="var(--green)" stroke-width="6"/>
    <path d="M0,270 C50,350 170,376 300,370 C440,362 575,318 720,304 L720,413 L0,413 Z" fill="var(--navy)"/>
  </svg>

  <div class="brand">
    <span class="brand__mark" aria-hidden="true"></span>
    <span class="brand__name">Varden Therapy</span>
  </div>

  <div class="divider"></div>

  <div class="details">
    <h1 class="details__name">LUKE VARDEN</h1>
    <p class="details__creds">BSc(kin), MPT, CAFCI, IMS</p>
    <ul class="contact">
      <li>
        <svg viewBox="0 0 20 20" aria-hidden="true"><circle cx="10" cy="10" r="8.6" fill="none" stroke="var(--navy)" stroke-width="1.6"/><path d="M6.5,5.5 L8.3,5.3 L9,7.6 L8,8.6 C8.6,10 9.9,11.3 11.4,12 L12.4,11 L14.6,11.7 L14.5,13.5 C11,14.2 5.8,9 6.5,5.5Z" fill="var(--navy)"/></svg>
        867-555-0142
      </li>
      <li>
        <svg viewBox="0 0 20 20" aria-hidden="true"><circle cx="10" cy="10" r="8.6" fill="none" stroke="var(--navy)" stroke-width="1.6"/><rect x="5.5" y="7" width="9" height="6.5" fill="var(--navy)"/><path d="M5.5,7 L10,10.6 L14.5,7" fill="none" stroke="#fff" stroke-width="1"/></svg>
        VardenTherapy@postnest.ca
      </li>
      <li>
        <svg viewBox="0 0 20 20" aria-hidden="true"><g fill="none" stroke="var(--navy)" stroke-width="1.4"><circle cx="10" cy="10" r="8.4"/><ellipse cx="10" cy="10" rx="3.6" ry="8.4"/><path d="M1.6,10 H18.4 M3,5.6 H17 M3,14.4 H17"/></g></svg>
        www.VardenTherapy.ca
      </li>
    </ul>
    <h2 class="services__title">Services Including</h2>
    <p class="services__row"><span>Physiotherapy</span><span>Direct Billing</span></p>
    <p class="services__row services__row--second"><span>Ims</span><span>Acupuncture</span></p>
  </div>

  <p class="slogan">Mobile Physiotherapy - Your Road To Recovery</p>
</section>

<section class="card card--back" aria-label="Back of business card">
  <div class="brand">
    <span class="brand__mark" aria-hidden="true"></span>
    <span class="brand__name">Varden Therapy</span>
  </div>
  <div class="social">
    <span class="social__item"><span class="social__mark" aria-hidden="true"></span>VardenTherapy</span>
    <span class="social__item"><span class="social__mark" aria-hidden="true"></span>@VardenTherapy</span>
  </div>
</section>

</body>
</html>
```